Technical Communications firm needs an article turned into a white paper

We want to redesign a 3-part blog series into a white paper that we can print for a conference. I've consolidated the three posts into the attached Word document.

We are looking for a light, easy to read design. Good use of graphics to support the message. I've added the graphics we used in the original post.

You can view them at
http://www.brightquillpages.com/blog/are-you-satisfied-with-your-dita-solution/

Target Market(s)

Product managers from High-tech, Finance, and Medical industries.

Industry/Entity Type

Information Technology

Colors

Designer to choose colors to be used in the design.

Requirements
Must have
• Must be modern, light, easy to read and slick design. Try to incorporate the graphics provided, but feel free to add more. Must retain the lists and tables.
• Must align with our website/brand.
• Must be easy to read. So not too busy.
• Please move all footnotes to endnotes. You'll need to rework the numbering.
Nice to have
• Awesome coverpage.
Should not have
• Hokey clipart. Not too heavy or hard to read.

```html
<!DOCTYPE html>
<html lang="en">
<head>
<meta charset="utf-8">
<title>Management – DITA Satisfaction White Paper</title>
<link href="https://fonts.googleapis.com/css2?family=Open+Sans:wght@600;700&family=Carlito:wght@400;700&display=swap" rel="stylesheet">
<style>
  :root {
    --navy: #1b1f93;
    --sky: #1aa6e4;
    --ink: #2b2b2b;
    --rule: #9ab8d6;
    --paper: #ffffff;
  }
  * { margin: 0; padding: 0; box-sizing: border-box; }
  html, body { width: 927px; height: 1200px; overflow: hidden; background: var(--paper); }
  .page {
    position: relative;
    width: 927px;
    height: 1200px;
    font-family: "Carlito", "Calibri", sans-serif;
    color: var(--ink);
  }
  .brand {
    position: absolute;
    left: 84px; top: 58px;
    display: flex; align-items: center; gap: 12px;
  }
  .brand-mark {
    width: 70px; height: 70px; border-radius: 50%;
    background: var(--navy);
  }
  .brand-name {
    font-family: "Open Sans", sans-serif;
    font-weight: 700;
    font-size: 23px;
    line-height: 1.05;
    color: var(--navy);
    letter-spacing: 0.2px;
  }
  .margin-rule {
    position: absolute;
    left: 111px; top: 128px;
    width: 3px; height: 932px;
    background: var(--navy);
  }
  .page-number {
    position: absolute;
    left: 744px; top: 70px;
    width: 126px; height: 28px;
    border-top: 1px solid var(--rule);
    border-bottom: 1px solid var(--rule);
    font-family: "Open Sans", sans-serif;
    font-weight: 700;
    font-size: 14px;
    color: var(--navy);
    line-height: 26px;
    text-align: center;
    letter-spacing: 1px;
  }
  .section-title {
    position: absolute;
    left: 174px; width: 696px; top: 148px;
    text-align: center;
    font-family: "Open Sans", sans-serif;
    font-weight: 700;
    font-size: 47px;
    color: var(--navy);
  }
  .section-title span { text-decoration: underline; text-decoration-thickness: 3px; text-underline-offset: 5px; }
  .hero {
    position: absolute;
    left: 178px; top: 216px;
    width: 692px; height: 292px;
    background: linear-gradient(135deg, #c9dcee 0%, #e6eef6 40%, #f0b324 55%, #d8e6f2 75%, #bcd4ea 100%);
  }
  .intro {
    position: absolute;
    left: 174px; width: 696px; top: 538px;
    font-size: 15.5px; line-height: 18.5px;
  }
  .intro .lede { text-align: center; padding: 0 6px; }
  .intro .follow { text-align: justify; text-indent: 28px; margin-top: 0; line-height: 22px; }
  sup { font-size: 9px; }
  .subhead {
    position: absolute;
    left: 174px; width: 696px; top: 708px;
    text-align: center;
    font-family: "Open Sans", sans-serif;
    font-weight: 700;
    font-size: 30px;
    color: var(--navy);
  }
  .subhead span { text-decoration: underline; text-decoration-thickness: 2px; text-underline-offset: 4px; }
  .body {
    position: absolute;
    left: 174px; width: 696px; top: 766px;
    font-size: 15.5px; line-height: 22.5px;
  }
  .body .lead { padding-left: 28px; }
  .issues { list-style: none; margin: 12px 0 12px 82px; }
  .issues li { position: relative; padding-left: 27px; text-align: justify; margin-bottom: 2px; }
  .issues li::before {
    content: ""; position: absolute; left: 2px; top: 8px;
    width: 6px; height: 6px; border-radius: 50%; background: var(--navy);
  }
  .body .closing { text-align: justify; }
  .dot-row { position: absolute; left: 104px; top: 1071px; }
</style>
</head>
<body>
<div class="page">
  <header class="brand">
    <div class="brand-mark"></div>
    <div class="brand-name">BRIGHTQUILL<br>PAGES</div>
  </header>
  <div class="margin-rule"></div>
  <div class="page-number">PAGE 11</div>

  <h1 class="section-title">3) <span>Management</span></h1>

  <div class="hero" role="img" aria-label="Photograph of a cluster of tangled road signs with arrows pointing in every direction against a cloudy blue sky"></div>

  <section class="intro">
    <p class="lede">This section is part of a series based on the results of a survey of more than 250 technical communication professionals conducted by The Markup Roundup in 2017 entitled The DITA Satisfaction Survey<sup>7</sup>. In the survey, almost two-thirds of respondents voiced some concerns with their DITA deployment.</p>
    <p class="follow">In my previous article in the series, I examined some of the principle issues related to technology. This last article in the series looks at the role management can play in improving user satisfaction with DITA.</p>
  </section>

  <h2 class="subhead"><span>&nbsp;Issues Related to Management</span></h2>

  <section class="body">
    <p class="lead">The lowest ranked reported issues fall under the category of management. These include</p>
    <ul class="issues">
      <li>We are impeded by a lack of governance. Ranked 6th by 60% of respondents</li>
      <li>We cannot find the right people to fill key roles. Ranked 7th by 57% of respondents, and</li>
      <li>We are unable to measure success. Ranked 9th by 55% of respondents.</li>
    </ul>
    <p class="closing">While these issues appear to be of least concern to many respondents, they are most likely to form the root cause of all other issues identified in the survey. This points to a general lack of awareness as to the role management should be playing in collaborative, structured authoring solutions.</p>
  </section>

  <svg class="dot-row" width="768" height="14" viewBox="0 0 768 14" aria-hidden="true">
    <g fill="var(--navy)">
      <circle cx="7" cy="7" r="6.5"/><circle cx="53" cy="7" r="6.5"/><circle cx="99" cy="7" r="6.5"/><circle cx="145" cy="7" r="6.5"/><circle cx="191" cy="7" r="6.5"/><circle cx="237" cy="7" r="6.5"/><circle cx="283" cy="7" r="6.5"/><circle cx="329" cy="7" r="6.5"/><circle cx="375" cy="7" r="6.5"/><circle cx="421" cy="7" r="6.5"/><circle cx="467" cy="7" r="6.5"/><circle cx="513" cy="7" r="6.5"/><circle cx="559" cy="7" r="6.5"/><circle cx="605" cy="7" r="6.5"/><circle cx="651" cy="7" r="6.5"/><circle cx="697" cy="7" r="6.5"/><circle cx="743" cy="7" r="6.5"/>
    </g>
    <g fill="var(--sky)">
      <circle cx="30" cy="7" r="6.5"/><circle cx="76" cy="7" r="6.5"/><circle cx="122" cy="7" r="6.5"/><circle cx="168" cy="7" r="6.5"/><circle cx="214" cy="7" r="6.5"/><circle cx="260" cy="7" r="6.5"/><circle cx="306" cy="7" r="6.5"/><circle cx="352" cy="7" r="6.5"/><circle cx="398" cy="7" r="6.5"/><circle cx="444" cy="7" r="6.5"/><circle cx="490" cy="7" r="6.5"/><circle cx="536" cy="7" r="6.5"/><circle cx="582" cy="7" r="6.5"/><circle cx="628" cy="7" r="6.5"/><circle cx="674" cy="7" r="6.5"/><circle cx="720" cy="7" r="6.5"/><circle cx="761" cy="7" r="6.5"/>
    </g>
  </svg>
</div>
</body>
</html>
```